Fence Contractor Website Design

We are working with Yard Shield. They are a local fencing and automatic gate installer and in need of a new website design.
Some sites to use for inspiration:
https://pelmorfence.example
https://tarvikfence.example
https://www.bristowdecksandfence.example
https://www.railquestinc.example
Thank you for taking the time to consider designing a website for us. We are web developers based in Stockton, CA, USA. Most of our projects go through the same process. Understanding this process may help you win a project with us. We custom-code all of our websites in-house. We don’t have any requirements as to what tools you use for your design, but we prefer Figma files. For any design that we label as four-stars, we send it to the client for review. The client picks the final design they want us to use. Once we complete this process, we will continue to show additional clients all the four-star sites and purchase them later. Your designs will have multiple chances to sell. For better chances of success, we ask that you follow these guidelines.
IMAGES:
If you use any images or icons in the design, we ask that you have a link to the asset so we can purchase the image/icon. Most of the designs we submit do not have the customer’s images on them unless they have some great images. Be creative; show us the feeling you are trying to portray with your image choices. Use any royalty-free site you choose. We subscribe to Veltrix and mainly use their images, but we can purchase images outside of Veltrix.
PLEASE NOTE: we will not submit designs to clients with watermarks on the images.
FONTS:
We ask that you identify the fonts used in the design. This can be done in a message if you want. We typically use Google Fonts and Veltrix Fonts.
CONTENT:
We're always open to different content and ideas. We often submit designs with stock images so the client can see our vision. We typically take pictures after the website launch to use their images with our vision. Lorem Ipsum is fine for paragraphs, but we ask that you write the headers in correct English. We want to be able to show the vision and identify the sections of the website.
INSPIRATION:
We typically add a couple of links in the brief of websites we like to help you get started in your design.
REVISIONS:
We do not often ask for revisions of the designs unless we see something in the design that may not appeal to the client. If there are slight changes that we want to make, we do that in the development process.
FEEDBACK:
We rarely give feedback on designs during the design process. We are working on many website projects and do not have the time to provide feedback. We usually respond if your request is well thought out and asks specific questions, but a note asking “feedback, please” usually goes unanswered.

```html
<!DOCTYPE html>
<html lang="en">
<head>
<meta charset="utf-8">
<title>Yard Shield — Fencing &amp; Gates</title>
<link href="https://fonts.googleapis.com/css2?family=Nunito+Sans:wght@400;600;700;800&display=swap" rel="stylesheet">
<style>
:root{
  --red:#d7261e;
  --ink:#1d1d1d;
  --text:#444;
  --muted:#6b6b6b;
  --light:#f3f3f3;
  --dark:#1b1b1b;
  --white:#fff;
}
*{box-sizing:border-box;margin:0;padding:0}
html,body{width:1200px;height:5329px;overflow:hidden}
body{font-family:"Nunito Sans",Arial,sans-serif;color:var(--text);background:var(--white);position:relative}
.abs{position:absolute}
.ph{position:absolute}
.btn{position:absolute;background:var(--red);color:#fff;font-size:11px;font-weight:700;text-transform:uppercase;display:flex;align-items:center;justify-content:center;letter-spacing:.3px}
.eyebrow{position:absolute;color:var(--red);font-size:13px;letter-spacing:2px;text-transform:uppercase}
.title{position:absolute;color:var(--ink);font-size:30px;font-weight:700;text-transform:uppercase;line-height:1.1}
.lorem{font-size:12.5px;line-height:1.5;color:var(--muted)}

/* header */
.site-header{position:absolute;left:0;top:0;width:1200px;height:75px;background:#fff}
.brand-tab{position:absolute;left:72px;top:0;width:118px;height:104px;background:#fff;clip-path:polygon(0 0,100% 0,100% 70%,50% 100%,0 70%);z-index:3;display:flex;flex-direction:column;align-items:center;justify-content:center;gap:6px;padding-bottom:20px}
.brand-name{font-weight:800;font-size:15px;color:var(--ink)}
.brand-dot{width:14px;height:14px;background:var(--red)}
.nav{position:absolute;left:334px;top:30px;display:flex;gap:20px;font-size:12px;font-weight:600;color:var(--ink);text-transform:uppercase}
.nav-phone{position:absolute;left:846px;top:29px;font-size:12px;font-weight:600;color:var(--ink);display:flex;gap:6px;align-items:center}

/* hero */
.hero{position:absolute;left:0;top:75px;width:1200px;height:589px}
.hero h1{position:absolute;top:70px;width:100%;text-align:center;font-size:39px;font-weight:800;color:var(--ink);text-transform:uppercase}
.hero h1 span{color:var(--red)}
.hero p{position:absolute;top:124px;left:290px;width:620px;text-align:center;font-size:19px;line-height:1.65;color:#333}

/* stats */
.stat{position:absolute;width:310px;height:124px;display:flex;flex-direction:column;align-items:center;justify-content:center}
.stat b{font-size:28px;font-weight:800;color:var(--ink)}
.stat span{font-size:18px;color:#333}

/* services */
.card{position:absolute;top:1686px;width:244px;height:379px;background:#f4f4f4}
.card .ph{left:12px;top:14px;width:220px;height:156px}
.card h3{position:absolute;left:12px;top:184px;font-size:18px;font-weight:700;color:var(--ink)}
.card p{position:absolute;left:12px;top:218px;width:220px}
.card .btn{left:12px;top:332px;width:156px;height:36px}

/* gallery */
.tile{position:absolute;width:388px;height:249px}

/* testimonials */
.quote-card{position:absolute;top:3203px;width:280px}
.avatar{position:absolute;left:0;top:0;width:62px;height:62px}
.qname{position:absolute;left:76px;top:8px;font-size:14px;font-weight:700;color:var(--ink)}
.qrole{position:absolute;left:76px;top:28px;font-size:9px;color:var(--muted)}
.stars{position:absolute;left:76px;top:40px;color:#f2b01e;font-size:11px;letter-spacing:1px}
.qhead{position:absolute;left:0;top:78px;font-size:16px;font-weight:700;color:var(--ink)}
.qtext{position:absolute;left:0;top:104px;width:258px;font-size:12px}

/* features */
.feature{position:absolute;width:290px}
.ficon{width:46px;height:46px;background:var(--red);display:flex;align-items:center;justify-content:center}
.feature h4{margin-top:16px;font-size:14px;font-weight:700;color:var(--ink);line-height:1.3}
.feature p{margin-top:6px;font-size:12px}

/* contact strip */
.strip{position:absolute;left:0;top:4262px;width:1200px;height:128px;background:var(--dark)}
.strip-item{position:absolute;top:38px;display:flex;gap:22px;color:#fff}
.strip-item small{display:block;font-size:12px;color:#bbb}
.strip-item div{font-size:14px;line-height:1.5}

/* form */
.label{position:absolute;font-size:11px;font-weight:700;color:var(--ink);text-transform:uppercase}
.field{position:absolute;background:#f1f1f1;height:38px}

/* footer */
.footer{position:absolute;left:0;top:5034px;width:1200px;height:275px;background:var(--dark);color:#ddd}
.fcol{position:absolute;top:54px;font-size:14px;line-height:1.7}
.fcol h5{font-size:14px;font-weight:700;color:#fff;text-transform:uppercase;margin-bottom:8px}
.frow{display:flex;gap:12px;align-items:flex-start;margin-bottom:8px}
.ficn{width:14px;height:14px;flex:none;margin-top:5px}
.copy{position:absolute;left:0;top:5309px;width:1200px;height:20px;text-align:center;font-size:12px;color:#444;background:#fff;line-height:20px}
</style>
</head>
<body>

<header class="site-header">
  <div class="brand-tab"><span class="brand-dot"></span><span class="brand-name">Yard Shield</span></div>
  <nav class="nav"><span>Home</span><span>About Us</span><span>Services</span><span>Testimonials</span><span>Gallery</span><span>Contact Us</span></nav>
  <div class="nav-phone">
    <svg width="14" height="14" viewBox="0 0 24 24"><path fill="#d7261e" d="M6.6 10.8a15 15 0 0 0 6.6 6.6l2.2-2.2c.3-.3.7-.4 1-.2 1.1.4 2.3.6 3.6.6.6 0 1 .4 1 1V20c0 .6-.4 1-1 1A17 17 0 0 1 3 4c0-.6.4-1 1-1h3.5c.6 0 1 .4 1 1 0 1.3.2 2.5.6 3.6.1.3 0 .7-.2 1z"/></svg>
    123-456-7890
  </div>
  <div class="btn" style="left:969px;top:19px;width:156px;height:38px;font-size:12px;text-transform:uppercase">Get A Free Quote</div>
</header>

<section class="hero">
  <div class="ph" role="img" aria-label="Long modern metal security fence with a sliding automatic gate beside a commercial building" style="inset:0;background:linear-gradient(180deg,#eef1f4 0%,#dfe3e7 45%,#b9bcbc 70%,#8e7b56 100%)"></div>
  <h1>Secure. Stylish. <span>Built To Last</span></h1>
  <p>Professional fencing and automatic gate solutions tailored to your property.</p>
  <div class="btn" style="left:521px;top:219px;width:157px;height:36px">Our Services</div>
</section>

<section class="about">
  <div class="ph" role="img" aria-label="Blue house behind a white picket fence with lilac bushes" style="left:77px;top:728px;width:267px;height:385px;background:linear-gradient(180deg,#dfe6ea,#7d8fa7 50%,#f2f2f2 85%)"></div>
  <div class="ph" role="img" aria-label="White picket garden gate framed by flowering shrubs" style="left:362px;top:786px;width:269px;height:389px;background:linear-gradient(180deg,#6f8b4a,#9ab169 55%,#eef0ea 80%,#c9c9c4)"></div>
  <div class="eyebrow" style="left:683px;top:797px">Who We Are</div>
  <div class="title" style="left:683px;top:819px">About Us</div>
  <p class="abs" style="left:683px;top:869px;width:442px;font-size:13.5px;line-height:1.6;color:#444">Yard Shield is your trusted local partner for high-quality fencing and automatic gate installations. With years of experience serving homeowners and businesses, we specialize in combining durability, functionality, and style to create boundaries that protect and enhance your property. Our skilled team is committed to delivering exceptional workmanship, using premium materials and modern technology for every project.</p>
  <div class="btn" style="left:683px;top:1074px;width:155px;height:35px">Read More</div>
</section>

<section class="stats">
  <div class="ph" role="img" aria-label="White picket fence under a flowering tree" style="left:0;top:1283px;width:290px;height:248px;background:linear-gradient(180deg,#5f7a43,#a1aa84 55%,#efefea)"></div>
  <div class="stat" style="left:290px;top:1283px;background:#fff"><b>60+</b><span>Years Of Expertise</span></div>
  <div class="stat" style="left:600px;top:1283px;background:#f1f1f1"><b>100+</b><span>Trusted Clients</span></div>
  <div class="stat" style="left:290px;top:1407px;background:#f1f1f1"><b>1000+</b><span>Completed Projects</span></div>
  <div class="stat" style="left:600px;top:1407px;background:#fff"><b>800+</b><span>Positive Reviews</span></div>
  <div class="ph" role="img" aria-label="White picket gate with a rose arbor" style="left:910px;top:1283px;width:290px;height:248px;background:linear-gradient(180deg,#5f7a43,#a1aa84 55%,#efefea)"></div>
</section>

<section class="services">
  <div class="eyebrow" style="left:77px;top:1598px">What We Do</div>
  <div class="title" style="left:77px;top:1622px">Our Services</div>
  <article class="card" style="left:77px">
    <div class="ph" role="img" aria-label="House with a white picket fence and flower beds" style="background:linear-gradient(180deg,#9fb7cf,#c9b98f 55%,#6c8a4b)"></div>
    <h3>Residential Fencing</h3>
    <p class="lorem">Lorem ipsum dolor sit amet consectetur. Felis hac id arcu sit sed. Est ornare amet felis in turpis tortor placerat. Adipiscing aliquam orci arcu sed montes</p>
    <div class="btn">Read More</div>
  </article>
  <article class="card" style="left:343px">
    <div class="ph" role="img" aria-label="Industrial building with a long metal perimeter fence" style="background:linear-gradient(180deg,#b9cbe0,#e1e4e7 55%,#9c9c98)"></div>
    <h3>Commercial Fencing</h3>
    <p class="lorem">Lorem ipsum dolor sit amet consectetur. Felis hac id arcu sit sed. Est ornare amet felis in turpis tortor placerat. Adipiscing aliquam orci arcu sed montes</p>
    <div class="btn">Read More</div>
  </article>
  <article class="card" style="left:612px">
    <div class="ph" role="img" aria-label="Worker repairing a chain link fence with a drill" style="background:linear-gradient(135deg,#56643c,#a68a5a 55%,#3b3f35)"></div>
    <h3>Fence Repairs</h3>
    <p class="lorem">Lorem ipsum dolor sit amet consectetur. Felis hac id arcu sit sed. Est ornare amet felis in turpis tortor placerat. Adipiscing aliquam orci arcu sed montes</p>
    <div class="btn">Read More</div>
  </article>
  <article class="card" style="left:879px">
    <div class="ph" role="img" aria-label="Modern house with a metal automatic driveway gate" style="background:linear-gradient(180deg,#d8dde2,#8a8a86 55%,#6e7a55)"></div>
    <h3>Automatic Gate</h3>
    <p class="lorem">Lorem ipsum dolor sit amet consectetur. Felis hac id arcu sit sed. Est ornare amet felis in turpis tortor placerat. Adipiscing aliquam orci arcu sed montes</p>
    <div class="btn">Read More</div>
  </article>
</section>

<section class="cta abs" style="left:0;top:2131px;width:1200px;height:321px;background:var(--light)">
  <h2 class="abs" style="top:62px;width:100%;text-align:center;font-size:28px;font-weight:700;color:var(--ink);text-transform:uppercase">Let's Build Your Perfect Fence</h2>
  <p class="abs" style="left:150px;top:106px;width:900px;text-align:center;font-size:13.5px;line-height:1.6;color:#444">Yard Shield is your trusted local partner for high-quality fencing and automatic gate installations. With years of experience serving homeowners and businesses, we specialize in combining durability, functionality, and style to create boundaries that protect and enhance your property. Our skilled team is committed to delivering exceptional workmanship, using premium materials and modern technology for every project.</p>
  <div class="btn" style="left:521px;top:226px;width:157px;height:34px">Get A Free Quote</div>
</section>

<section class="gallery">
  <div class="eyebrow" style="left:77px;top:2516px">Our Work Gallery</div>
  <div class="title" style="left:77px;top:2540px">Crafted With Precision</div>
  <div class="abs" style="left:962px;top:2555px;font-size:14px;color:var(--red);display:flex;gap:10px;align-items:center">View Our All Work
    <svg width="22" height="10" viewBox="0 0 22 10"><path d="M0 5h20M16 1l4 4-4 4" stroke="#d7261e" stroke-width="1.6" fill="none"/></svg></div>
  <div class="tile" role="img" aria-label="Horizontal slatted wood fence beside a garage" style="left:0;top:2605px;background:linear-gradient(135deg,#8c6a48,#c8b79d 50%,#6f5a45)"></div>
  <div class="tile" role="img" aria-label="Cottage with a white picket fence" style="left:405px;top:2605px;background:linear-gradient(180deg,#86b1dd,#d7cdb3 55%,#6e8c4d)"></div>
  <div class="tile" role="img" aria-label="White colonial house with picket fence" style="left:811px;top:2605px;background:linear-gradient(180deg,#c7d3dc,#eaeaea 55%,#7d9152)"></div>
  <div class="tile" role="img" aria-label="Ornate black wrought iron gates" style="left:0;top:2872px;background:linear-gradient(135deg,#2a3038,#6e7c62 50%,#1f242a)"></div>
  <div class="tile" role="img" aria-label="Brick pillar fence with metal panels" style="left:405px;top:2872px;background:linear-gradient(135deg,#7c3b2c,#8c8f7c 50%,#5f6c3b)"></div>
  <div class="tile" role="img" aria-label="Faded white house and fence" style="left:811px;top:2872px;background:linear-gradient(180deg,#edf0f2,#f4f4f2)"></div>
  <div class="abs" style="left:918px;top:2980px;width:176px;height:35px;border:1.5px solid #555;display:flex;align-items:center;justify-content:center;font-size:12px;color:#333;text-transform:uppercase">View More</div>
</section>

<section class="testimonials">
  <svg class="abs" style="left:77px;top:3203px" width="160" height="80" viewBox="0 0 160 80"><path d="M10 0h50L40 80H0zM90 0h50l-20 80H80z" fill="#e6e6e6"/></svg>
  <div class="eyebrow" style="left:77px;top:3272px">Testimonials</div>
  <div class="title" style="left:77px;top:3294px">What Our Clients Say</div>
  <p class="abs lorem" style="left:77px;top:3336px;width:360px">Lorem ipsum dolor sit amet consectetur. Tristique justo venenatis facilisis tellus amet sit bibendum bibendum et. Cras auctor nisi odio id elementum phasellus felis</p>
  <div class="abs" style="left:77px;top:3410px;width:30px;height:30px;display:flex;align-items:center;justify-content:center"><svg width="20" height="10" viewBox="0 0 20 10"><path d="M20 5H2M6 1L2 5l4 4" stroke="#d7261e" stroke-width="1.6" fill="none"/></svg></div>
  <div class="abs" style="left:121px;top:3410px;width:30px;height:30px;background:var(--red);display:flex;align-items:center;justify-content:center"><svg width="20" height="10" viewBox="0 0 20 10"><path d="M0 5h18M14 1l4 4-4 4" stroke="#fff" stroke-width="1.6" fill="none"/></svg></div>
  <div class="abs" style="left:518px;top:3205px;width:2px;height:90px;background:#ddd"></div>
  <div class="abs" style="left:843px;top:3205px;width:2px;height:90px;background:#ddd"></div>
  <div class="quote-card" style="left:536px;height:300px">
    <div class="avatar" role="img" aria-label="Client portrait" style="background:linear-gradient(135deg,#b48a62,#e6d6c3)"></div>
    <div class="qname">Lena Howard</div><div class="qrole">Home Owner, xyz place</div><div class="stars">★★★★★</div>
    <div class="qhead">Outstanding!</div>
    <p class="qtext lorem">Lorem ipsum dolor sit amet consectetur. Tristique justo venenatis facilisis tellus amet sit bibendum bibendum et. Cras auctor nisi odio id elementum phasellus felis vulputate aliquet. At consequat in iaculis semper dui feugiat elit tincidunt vel. Mollis cras feugiat nisi leo. Integer.</p>
  </div>
  <div class="quote-card" style="left:861px;height:300px">
    <div class="avatar" role="img" aria-label="Client portrait" style="background:linear-gradient(135deg,#b48a62,#e6d6c3)"></div>
    <div class="qname">Lena Howard</div><div class="qrole">Home Owner, xyz place</div><div class="stars">★★★★☆</div>
    <div class="qhead">Outstanding!</div>
    <p class="qtext lorem">Lorem ipsum dolor sit amet consectetur. Tristique justo venenatis facilisis tellus amet sit bibendum bibendum et. Cras auctor nisi odio id elementum phasellus felis vulputate aliquet. At consequat in iaculis semper dui feugiat elit tincidunt vel. Mollis cras feugiat nisi leo. Integer.</p>
  </div>
</section>

<section class="why">
  <div class="ph" role="img" aria-label="Yellow house with a white picket fence and pink roses" style="left:77px;top:3517px;width:529px;height:543px;background:linear-gradient(180deg,#e9eef0,#d9c27a 40%,#5d7a3c 70%,#f2f2f0)"></div>
  <div class="eyebrow" style="left:670px;top:3551px">Why Choose Us</div>
  <div class="title" style="left:670px;top:3575px;font-size:29px">Why Homeowners &amp;<br>Businesses Trust Yard Shield</div>
  <div class="abs" style="left:457px;top:3672px;width:666px;height:528px;background:var(--light)"></div>
  <div class="feature" style="left:491px;top:3715px">
    <div class="ficon"><svg width="26" height="26" viewBox="0 0 26 26" fill="none" stroke="#fff" stroke-width="1.6"><rect x="5" y="3" width="16" height="20"/><path d="M9 9h8M9 13h8M9 17h5"/></svg></div>
    <h4>Experienced And Certified Installation Team</h4>
    <p class="lorem">Lorem ipsum dolor sit amet consectetur. Tristique justo venenatis facilisis tellus amet sit bibendum bibendum et. Cras auctor nisi odio id elementum phasellus felis vulputate aliquet. At consequat in iaculis semper dui</p>
  </div>
  <div class="feature" style="left:808px;top:3715px">
    <div class="ficon"><svg width="26" height="26" viewBox="0 0 26 26" fill="none" stroke="#fff" stroke-width="1.6"><circle cx="13" cy="13" r="9"/><path d="M9 13l3 3 5-6"/></svg></div>
    <h4>Premium Materials For Lasting Performance</h4>
    <p class="lorem">Lorem ipsum dolor sit amet consectetur. Tristique justo venenatis facilisis tellus amet sit bibendum bibendum et. Cras auctor nisi odio id elementum phasellus felis vulputate aliquet. At consequat in iaculis semper dui</p>
  </div>
  <div class="feature" style="left:491px;top:3961px">
    <div class="ficon"><svg width="26" height="26" viewBox="0 0 26 26" fill="none" stroke="#fff" stroke-width="1.6"><circle cx="13" cy="13" r="4"/><circle cx="13" cy="13" r="9" stroke-dasharray="3 2"/></svg></div>
    <h4>Exceptional Customer Service From Start To Finish</h4>
    <p class="lorem">Lorem ipsum dolor sit amet consectetur. Tristique justo venenatis facilisis tellus amet sit bibendum bibendum et. Cras auctor nisi odio id elementum phasellus felis vulputate aliquet. At consequat in iaculis semper dui</p>
  </div>
  <div class="feature" style="left:808px;top:3961px">
    <div class="ficon"><svg width="26" height="26" viewBox="0 0 26 26" fill="none" stroke="#fff" stroke-width="1.6"><path d="M4 12l9-7 9 7v10H4z"/><path d="M10 22v-6h6v6"/></svg></div>
    <h4>Transparent Pricing And Free Estimates</h4>
    <p class="lorem">Lorem ipsum dolor sit amet consectetur. Tristique justo venenatis facilisis tellus amet sit bibendum bibendum et. Cras auctor nisi odio id elementum phasellus felis vulputate aliquet. At consequat in iaculis semper dui</p>
  </div>
</section>

<section class="strip">
  <div class="strip-item" style="left:228px">
    <svg width="34" height="34" viewBox="0 0 24 24"><path fill="#fff" d="M6.6 10.8a15 15 0 0 0 6.6 6.6l2.2-2.2c.3-.3.7-.4 1-.2 1.1.4 2.3.6 3.6.6.6 0 1 .4 1 1V20c0 .6-.4 1-1 1A17 17 0 0 1 3 4c0-.6.4-1 1-1h3.5c.6 0 1 .4 1 1 0 1.3.2 2.5.6 3.6.1.3 0 .7-.2 1z"/></svg>
    <div><small>Phone Number</small>123-456-7890</div>
  </div>
  <div class="strip-item" style="left:446px">
    <svg width="26" height="34" viewBox="0 0 24 32"><path fill="#fff" d="M12 0a11 11 0 0 0-11 11c0 8 11 21 11 21s11-13 11-21A11 11 0 0 0 12 0zm0 16a5 5 0 1 1 0-10 5 5 0 0 1 0 10z"/></svg>
    <div><small>Address</small>Lorem ipsum dolor sit amet<br>consectetur.</div>
  </div>
  <div class="strip-item" style="left:764px">
    <svg width="32" height="34" viewBox="0 0 32 24"><rect x="1" y="3" width="30" height="19" fill="none" stroke="#fff" stroke-width="2"/><path d="M1 3l15 11L31 3" stroke="#fff" stroke-width="2" fill="none"/></svg>
    <div><small>E-Mail Address</small>hello@yardshield.example</div>
  </div>
</section>

<section class="contact">
  <div class="eyebrow" style="left:77px;top:4453px">Contact Us</div>
  <div class="title" style="left:77px;top:4475px">Get In Touch</div>
  <p class="abs" style="left:77px;top:4516px;width:380px;font-size:12px;line-height:1.5;color:#444">Your property deserves security and style. Contact Yard Shield today to discuss your project and get a free estimate.</p>
  <div class="label" style="left:77px;top:4583px">First Name</div>
  <div class="field" style="left:77px;top:4606px;width:206px;background:#fff;border:1px solid var(--red)"></div>
  <div class="label" style="left:313px;top:4583px">Last Name</div>
  <div class="field" style="left:313px;top:4606px;width:206px"></div>
  <div class="label" style="left:77px;top:4656px">Email Address</div>
  <div class="field" style="left:77px;top:4679px;width:442px"></div>
  <div class="label" style="left:77px;top:4729px">Phone Number</div>
  <div class="field" style="left:77px;top:4752px;width:442px"></div>
  <div class="label" style="left:77px;top:4802px">Message</div>
  <div class="field" style="left:77px;top:4825px;width:442px;height:74px"></div>
  <div class="btn" style="left:77px;top:4932px;width:156px;height:36px">Submit</div>
  <div class="ph" role="img" aria-label="White vinyl privacy fence with red roses" style="left:567px;top:4485px;width:271px;height:392px;background:linear-gradient(180deg,#7d9a5a,#eeeeec 35%,#d8d8d6 70%,#5f7a3c)"></div>
  <div class="ph" role="img" aria-label="White vinyl fence along a lawn" style="left:854px;top:4603px;width:269px;height:332px;background:linear-gradient(180deg,#6f8f4a,#ecedea 40%,#c9c7be 70%,#6e8a45)"></div>
</section>

<footer class="footer">
  <div class="fcol" style="left:77px"><h5>Quick Links</h5>Home<br>About Us<br>Testimonials<br>Gallery<br>Career</div>
  <div class="fcol" style="left:219px;width:200px"><h5>Contact Info</h5>
    <div class="frow"><svg class="ficn" viewBox="0 0 24 24"><path fill="#fff" d="M6.6 10.8a15 15 0 0 0 6.6 6.6l2.2-2.2c.3-.3.7-.4 1-.2 1.1.4 2.3.6 3.6.6.6 0 1 .4 1 1V20c0 .6-.4 1-1 1A17 17 0 0 1 3 4c0-.6.4-1 1-1h3.5c.6 0 1 .4 1 1 0 1.3.2 2.5.6 3.6.1.3 0 .7-.2 1z"/></svg>123-456-7890</div>
    <div class="frow"><svg class="ficn" viewBox="0 0 24 32"><path fill="#fff" d="M12 0a11 11 0 0 0-11 11c0 8 11 21 11 21s11-13 11-21A11 11 0 0 0 12 0z"/></svg><span style="line-height:1.4">Lorem ipsum dolor sit amet consectetur.</span></div>
    <div class="frow"><svg class="ficn" viewBox="0 0 32 24"><rect x="1" y="3" width="30" height="19" fill="none" stroke="#fff" stroke-width="3"/></svg>hello@yardshield.example</div>
  </div>
  <div class="fcol" style="left:465px"><h5>Services</h5>Residential Fence<br>Commercial Fence<br>Fence Repair<br>Automatic Gate Installation</div>
  <div class="fcol" style="left:717px;width:200px"><h5>Contact Info</h5>
    <div class="frow"><svg class="ficn" viewBox="0 0 14 14"><circle cx="7" cy="7" r="6" fill="none" stroke="#fff" stroke-width="1.5"/></svg>yardshield</div>
    <div class="frow"><svg class="ficn" viewBox="0 0 14 14"><circle cx="7" cy="7" r="6" fill="none" stroke="#fff" stroke-width="1.5"/></svg><span style="line-height:1.4">Lorem ipsum dolor sit amet consectetur.</span></div>
    <div class="frow"><svg class="ficn" viewBox="0 0 14 14"><circle cx="7" cy="7" r="6" fill="none" stroke="#fff" stroke-width="1.5"/></svg><span style="line-height:1.4">Lorem ipsum dolor sit amet consectetur.</span></div>
  </div>
  <div class="abs" style="left:973px;top:0;width:152px;height:152px;background:#fff;clip-path:polygon(0 0,100% 0,100% 72%,50% 100%,0 72%);display:flex;flex-direction:column;align-items:center;justify-content:center;gap:6px;padding-bottom:24px">
    <span class="brand-dot"></span><span class="brand-name">Yard Shield</span>
  </div>
</footer>
<div class="copy">© 2025 Brookline Associates Real Estate</div>

</body>
</html>
```